Mobile welding fabrication and repair, heavy equipment and semi repair

We need a business card design that will catch the eye but look prelesional at the same time. Were based out of Idaho and we do all welding fabrication jobs and repairs, we also build and install custom pipe fences for personal or larger scale fence jobs and can give free quotes. We can do semi truck and trailer repairs Mobily also.

Target Market(s)

Welding

Industry/Entity Type

welding and repair

Contact Information for Business Card

email (ravenforgeandmend@mailbay.net, phone number 208-417-3826, owner (Dalton Whitcomb), Pipe Fence, Semi Repair, Mobile welding and fabrication

Font styles to use
Sans Serif

Requirements
Must have
• My logo in black background on one side , and other side my logo in white back round with all the information listed on card details
Nice to have
• make it stand out from other business cards

```html
<!DOCTYPE html>
<html lang="en">
<head>
<meta charset="utf-8">
<title>Raven Forge and Mend — Business Card</title>
<link rel="stylesheet" href="https://fonts.googleapis.com/css2?family=Montserrat:wght@400;500;700;800&display=swap">
<style>
  :root {
    --stage: #2b2b2d;
    --card-black: #141414;
    --card-white: #ffffff;
    --brand-blue: #1a73c9;
    --ink: #1d1d1f;
    --faint-blue: #e6f0f9;
    --band-text: #ffffff;
  }
  * { margin: 0; padding: 0; box-sizing: border-box; }
  html, body {
    width: 1200px; height: 1015px; overflow: hidden;
    background: var(--stage);
    font-family: "Montserrat", sans-serif;
  }
  .canvas { position: relative; width: 1200px; height: 1015px; }

  .card {
    position: absolute; width: 700px; height: 400px;
    box-shadow: 0 18px 40px rgba(0,0,0,.55);
    overflow: hidden;
  }

  /* Back side */
  .card--back { left: 80px; top: 80px; background: var(--card-black); }
  .card--back .pattern {
    position: absolute; inset: 0;
    background: linear-gradient(135deg, #1c1c1c 0%, #121212 60%, #181818 100%);
  }
  .card--back .wordmark {
    position: absolute; left: 0; right: 0; top: 170px;
    text-align: center;
    font-weight: 800; font-size: 34px; letter-spacing: 4px;
    color: var(--brand-blue);
  }

  /* Front side */
  .card--front { left: 420px; top: 535px; background: var(--card-white); }
  .card--front .emblem-area {
    position: absolute; left: 250px; top: 10px; width: 360px; height: 320px;
    border-radius: 90px;
    background: linear-gradient(160deg, #e3edf8 0%, #eaf3fb 70%, #f3f8fd 100%);
  }
  .identity {
    position: absolute; left: 170px; top: 40px; width: 460px;
    text-align: center;
  }
  .identity .brand-name {
    font-weight: 800; font-size: 78px; line-height: 1; letter-spacing: 4px;
    color: var(--brand-blue);
  }
  .identity .brand-tagline {
    font-weight: 800; font-size: 24px; letter-spacing: 2px;
    color: var(--ink); margin-top: 4px;
  }
  .contact { margin-top: 22px; }
  .contact .person {
    font-weight: 700; font-size: 28px; color: var(--brand-blue);
  }
  .contact .role {
    font-weight: 500; font-size: 17px; color: var(--ink); letter-spacing: 1px;
  }
  .contact .rule {
    width: 150px; height: 1px; background: var(--ink); margin: 6px auto 8px;
  }
  .contact .line {
    font-weight: 400; font-size: 17px; color: var(--ink); line-height: 1.45;
  }
  .services {
    position: absolute; left: 0; right: 0; bottom: 0; height: 44px;
    background: var(--card-black);
    display: flex; align-items: center; justify-content: center; gap: 12px;
    color: var(--band-text); font-weight: 500; font-size: 15px; letter-spacing: .5px;
  }
  .services .dot {
    width: 9px; height: 9px; border-radius: 50%; background: var(--brand-blue);
  }
</style>
</head>
<body>
<main class="canvas">

  <section class="card card--back" aria-label="Card back">
    <div class="pattern" role="img" aria-label="Tonal pattern of repeated company wordmarks on black"></div>
    <div class="wordmark">RAVEN</div>
  </section>

  <section class="card card--front" aria-label="Card front">
    <div class="emblem-area" role="img" aria-label="Large faint company emblem in pale blue"></div>
    <div class="identity">
      <div class="brand-name">RAVEN</div>
      <div class="brand-tagline">FORGE AND MEND</div>
      <div class="contact">
        <div class="person">DALTON WHITCOMB</div>
        <div class="role">OWNER</div>
        <div class="rule"></div>
        <div class="line">208-417-3826</div>
        <div class="line">ravenforgeandmend@mailbay.net</div>
      </div>
    </div>
    <div class="services">
      <span>FABRICATION</span><span class="dot"></span>
      <span>MOBILE WELDING</span><span class="dot"></span>
      <span>SEMI REPAIR</span><span class="dot"></span>
      <span>PIPE FENCE</span>
    </div>
  </section>

</main>
</body>
</html>
```